card for handyman and landscaping business, double sided with services listed on the back

Design a business card for a handyman and Landscaping business in San Jose,ca. Would like front to be a house with 3D characters doing different tasks i.e. Mowing lawn, painting, sprinklers, lighting, weed whacking, power washing, lumber etc. on the backside a cutout of the interior with computer, internet, cleaning, bathroom/kitchen remodeling, smart home etc.

Industry/Entity Type

Handyman

Contact Information for Business Card

Two sided view of a house, one outside services and one inside services

Colors

Designer to choose colors to be used in the design.

Requirements
Must have
• General Household Repairs and Maintenance
• Landscaping, Gardening, and Planting
• Painting, Patching and Trim/Moulding Work
• Cleaning, Restoring and Hauling/Trash Removal
• Blinds, Curtains, and Assembly Work
• Computer, Internet/Wireless, and Smart Home Service

```html
<!DOCTYPE html>
<html lang="en">
<head>
<meta charset="utf-8">
<title>Handyman, Landscaping and Tech Services – Business Card</title>
<link href="https://fonts.googleapis.com/css2?family=Source+Sans+3:wght@400;600;700&display=swap" rel="stylesheet">
<style>
  :root {
    --stage: #555555;
    --card-dark: #1b1b1b;
    --card-footer: #0f0f0f;
    --band-light: #ececec;
    --accent-green: #2e9a1c;
    --text-light: #ffffff;
    --icon-disc: #000000;
  }
  * { margin: 0; padding: 0; box-sizing: border-box; }
  html, body { width: 1200px; height: 900px; overflow: hidden; }
  body {
    background: var(--stage);
    font-family: "Source Sans 3", "Myriad Pro", sans-serif;
    color: var(--text-light);
    position: relative;
  }
  .card {
    position: absolute;
    top: 306px;
    width: 440px;
    height: 271px;
    background: var(--card-dark);
    box-shadow: 3px 4px 8px rgba(0,0,0,0.45);
    overflow: hidden;
  }
  .card--front { left: 149px; }
  .card--back { left: 608px; width: 441px; }
  .card__band { position: absolute; left: 0; top: 0; width: 100%; height: 100%; }
  .card__footer {
    position: absolute; left: 0; bottom: 0; width: 100%; height: 29px;
    background: var(--card-footer);
    text-align: center; font-size: 12.5px; line-height: 29px; letter-spacing: 0.2px;
  }
  .card__title {
    position: absolute; top: 27px; left: 0; width: 100%;
    text-align: center; color: var(--accent-green);
    font-weight: 700; font-size: 16.5px; letter-spacing: 0.2px;
  }
  .contact { position: absolute; left: 24px; top: 62px; font-size: 13px; line-height: 16px; }
  .contact__row { display: flex; align-items: center; gap: 7px; }
  .contact__row svg { width: 8px; height: 8px; fill: var(--accent-green); }
  .contact__address { margin-top: 10px; line-height: 16px; }
  .person { position: absolute; right: 24px; top: 63px; text-align: right; }
  .person__name { color: var(--accent-green); font-weight: 700; font-size: 16px; line-height: 18px; }
  .person__role { font-size: 13px; line-height: 15px; }
  .services {
    position: absolute; top: 17px; list-style: none;
    font-size: 11.5px; line-height: 14px;
  }
  .services--left { left: 18px; }
  .services--right { left: 270px; }
  .services li { position: relative; padding-left: 8px; }
  .services li::before {
    content: ""; position: absolute; left: 0; top: 5px;
    width: 4px; height: 4px; border-radius: 50%; background: var(--accent-green);
  }
  .icon-disc { fill: var(--icon-disc); }
  .icon-glyph { fill: var(--text-light); }
  .icon-line { fill: none; stroke: var(--text-light); stroke-width: 2; stroke-linecap: round; }
  .roof-fill { fill: var(--band-light); }
  .roof-edge { fill: none; stroke: var(--accent-green); stroke-width: 3; }
</style>
</head>
<body>

<section class="card card--front" aria-label="Business card front">
  <svg class="card__band" viewBox="0 0 440 271" aria-hidden="true">
    <path class="roof-fill" d="M0 167 H154 L219 136 L266 166 V143 H306 V167 H440 V242 H0 Z"/>
    <path class="roof-edge" d="M0 167 H154 L219 136 L266 166 V143 H306 V167 H440"/>
    <path d="M266 143 H306" stroke="var(--accent-green)" stroke-width="4"/>
    <!-- toilet -->
    <g transform="translate(56 210)">
      <circle class="icon-disc" r="25"/>
      <rect class="icon-glyph" x="-8" y="-15" width="16" height="10" rx="1"/>
      <path class="icon-glyph" d="M-10 -3 H10 Q10 6 4 8 L5 15 H-5 L-4 8 Q-10 6 -10 -3 Z"/>
    </g>
    <!-- broom -->
    <g transform="translate(121 210)">
      <circle class="icon-disc" r="25"/>
      <line class="icon-line" x1="9" y1="-14" x2="-1" y2="4"/>
      <path class="icon-glyph" d="M-4 2 L3 6 L-2 14 L-14 10 Z"/>
      <circle class="icon-glyph" cx="9" cy="12" r="1.5"/>
    </g>
    <!-- computer -->
    <g transform="translate(186 210)">
      <circle class="icon-disc" r="25"/>
      <rect class="icon-glyph" x="-13" y="-14" width="26" height="18" rx="1"/>
      <path d="M-5 -6 Q0 -10 5 -6 M-2.5 -3 Q0 -5 2.5 -3" stroke="#000" stroke-width="1.5" fill="none"/>
      <rect class="icon-glyph" x="-13" y="7" width="26" height="6" rx="1"/>
    </g>
    <!-- wireless tower -->
    <g transform="translate(252 210)">
      <circle class="icon-disc" r="25"/>
      <path class="icon-line" d="M-6 -6 Q-9 0 -6 6 M6 -6 Q9 0 6 6 M-11 -10 Q-16 0 -11 10 M11 -10 Q16 0 11 10" stroke-width="1.6"/>
      <path class="icon-glyph" d="M-1 -4 H1 L5 14 H-5 Z"/>
      <circle class="icon-glyph" cy="-4" r="2.5"/>
    </g>
    <!-- light bulb -->
    <g transform="translate(317 210)">
      <circle class="icon-disc" r="25"/>
      <circle class="icon-glyph" cy="-3" r="7"/>
      <rect class="icon-glyph" x="-3.5" y="4" width="7" height="6"/>
      <path class="icon-line" d="M0 -16 V-13 M-11 -3 H-14 M11 -3 H14 M-8 -11 L-10 -13 M8 -11 L10 -13" stroke-width="1.5"/>
    </g>
    <!-- smart home -->
    <g transform="translate(384 210)">
      <circle class="icon-disc" r="25"/>
      <path class="icon-glyph" d="M0 -15 L14 -2 H10 V14 H-10 V-2 H-14 Z"/>
      <path d="M-3.5 0 A5 5 0 1 0 3.5 0 M0 -3 V3" stroke="#000" stroke-width="1.8" fill="none" stroke-linecap="round"/>
    </g>
  </svg>

  <h1 class="card__title">HANDYMAN , LANDSCAPING AND TECH SERVICES</h1>

  <div class="contact">
    <p class="contact__row"><svg viewBox="0 0 10 10" aria-hidden="true"><path d="M2 0 L4 2.5 L3 4 Q4.5 6 6 7 L7.5 6 L10 8 L8.5 10 Q3 9 0 1.5 Z"/></svg>(044)987654321</p>
    <p class="contact__row"><svg viewBox="0 0 10 10" aria-hidden="true"><path d="M0 2 H10 V8 H0 Z"/></svg>hello@oaklinehome.com</p>
    <p class="contact__address">5678, Maple Street Here,<br>Country name, 54321</p>
  </div>

  <div class="person">
    <p class="person__name">DANIEL REYES</p>
    <p class="person__role">Managing Director</p>
  </div>

  <p class="card__footer">www.oaklinehome.com</p>
</section>

<section class="card card--back" aria-label="Business card back">
  <svg class="card__band" viewBox="0 0 441 271" aria-hidden="true">
    <path class="roof-fill" d="M0 167 H155 L219 136 L268 166 V143 H308 V167 H441 V242 H0 Z"/>
    <path class="roof-edge" d="M0 167 H155 L219 136 L268 166 V143 H308 V167 H441"/>
    <path d="M268 143 H308" stroke="var(--accent-green)" stroke-width="4"/>
    <!-- lawn mower -->
    <g transform="translate(56 210)">
      <circle class="icon-disc" r="25"/>
      <path class="icon-line" d="M-16 -12 L-2 2"/>
      <path class="icon-glyph" d="M-6 0 H14 V8 H-6 Z"/>
      <circle class="icon-glyph" cx="-3" cy="10" r="4"/>
      <circle class="icon-glyph" cx="11" cy="10" r="4"/>
    </g>
    <!-- saw -->
    <g transform="translate(121 210)">
      <circle class="icon-disc" r="25"/>
      <path class="icon-glyph" d="M-8 -14 L-2 -16 L10 6 L4 8 Z"/>
      <rect class="icon-glyph" x="-15" y="8" width="30" height="3"/>
    </g>
    <!-- paint roller -->
    <g transform="translate(187 210)">
      <circle class="icon-disc" r="25"/>
      <rect class="icon-glyph" x="-12" y="-14" width="20" height="9" rx="2"/>
      <path class="icon-line" d="M8 -9 H12 V-1 H0 V4"/>
      <rect class="icon-glyph" x="-2.5" y="4" width="5" height="11" rx="1"/>
    </g>
    <!-- pressure washer -->
    <g transform="translate(252 210)">
      <circle class="icon-disc" r="25"/>
      <path class="icon-glyph" d="M-12 -4 H6 V0 H-4 L-6 10 H-10 L-9 0 H-12 Z"/>
      <path class="icon-line" d="M9 -2 L15 -5 M9 -2 L15 -2 M9 -2 L15 1" stroke-width="1"/>
    </g>
    <!-- bucket -->
    <g transform="translate(317 210)">
      <circle class="icon-disc" r="25"/>
      <path class="icon-glyph" d="M-10 -9 H10 L7 14 H-7 Z"/>
      <path class="icon-line" d="M-10 -9 Q0 -20 10 -9" stroke-width="1.5"/>
    </g>
    <!-- window -->
    <g transform="translate(392 210)">
      <circle class="icon-disc" r="25"/>
      <rect class="icon-glyph" x="-13" y="-13" width="26" height="26"/>
      <rect x="-10" y="-10" width="8.5" height="8.5" fill="#000"/>
      <rect x="1.5" y="-10" width="8.5" height="8.5" fill="#000"/>
      <rect x="-10" y="1.5" width="8.5" height="8.5" fill="#000"/>
      <rect x="1.5" y="1.5" width="8.5" height="8.5" fill="#000"/>
    </g>
  </svg>

  <ul class="services services--left">
    <li>Handyman</li>
    <li>Landscaping</li>
    <li>Sprinklers/Irrigation</li>
    <li>Painting</li>
    <li>Electrical</li>
    <li>Lighting</li>
    <li>Power Washing</li>
    <li>Hauling</li>
  </ul>
  <ul class="services services--right">
    <li>Cleaning</li>
    <li>Bath/Kitchen</li>
    <li>Baseboards/Trim/Moulding</li>
    <li>Smart Home</li>
    <li>A/C and Heating</li>
    <li>Blinds, Curtains</li>
    <li>Assembly Services</li>
    <li>Computer/Tech Service</li>
  </ul>

  <p class="card__footer">www.oaklinehome.com</p>
</section>

</body>
</html>
```